Brightfield Ventures Inc. Letterhead

Creation of attractive and eye catching letterhead for a business start-up for the construction industry. Letterhead must relate to construction, but avoid standard hammer and tools in the design.

I forgot to add some details, sorry about that. Some pertinent info: Ph: 916-555-0187 brightfieldventures.example 448 Willowmere Ave, Ste 210 Alder Bay, CA 95999 info@brightfieldventures.example not sure if slogan should be in there" “Bringing builders together for a stronger, purposeful trade.” must be able to be used in word. Thanks!

```html
<!DOCTYPE html>
<html lang="en">
<head>
<meta charset="utf-8">
<title>Brightfield Ventures Inc. Letterhead</title>
<link href="https://fonts.googleapis.com/css2?family=Arimo:wght@400;700&family=Raleway:wght@300&display=swap" rel="stylesheet">
<style>
  :root{
    --backdrop:#c3d3e8;
    --paper:#ffffff;
    --navy:#1b2a6b;
    --red:#cc2229;
    --ink:#1d1d1f;
    --muted:#6d6f75;
    --faint:#d9dbe0;
  }
  *{box-sizing:border-box;margin:0;padding:0}
  html,body{width:1200px;height:784px;overflow:hidden;background:var(--backdrop)}
  body{display:flex;align-items:center;justify-content:center;font-family:"Arimo",Arial,sans-serif}
  .letterhead{position:relative;width:572px;height:740px;background:var(--paper);overflow:hidden;box-shadow:0 4px 18px rgba(40,60,100,.18)}
  .brand{position:absolute;left:62px;top:48px;display:flex;align-items:center;gap:8px}
  .brand-mark{width:12px;height:12px;background:var(--navy)}
  .brand-name{font-size:17px;font-weight:700;color:var(--navy)}
  .brand-rule{position:absolute;left:62px;top:76px;width:150px;height:1px;background:var(--red)}
  .contact{position:absolute;right:58px;top:46px;text-align:right;font-style:normal;font-size:7.5px;line-height:12px;color:var(--muted)}
  .contact-name{font-size:10px;font-weight:700;color:var(--red);margin-bottom:2px}
  .contact-line{display:flex;justify-content:flex-end;align-items:center;gap:5px}
  .dot{width:5px;height:5px;border-radius:50%;background:var(--red)}
  .body-copy{position:absolute;left:62px;top:128px;width:410px;font-size:10px;line-height:13.5px;color:var(--ink)}
  .body-copy p{margin-bottom:13px}
  .signature{position:absolute;left:100px;top:505px;width:130px;height:46px;background:linear-gradient(90deg,#eef0f4,#f7f8fa)}
  .corner{position:absolute;left:0;bottom:0}
  .watermark{position:absolute;left:160px;top:624px;font-size:26px;font-weight:700;color:var(--faint)}
  .slogan{position:absolute;right:22px;top:100px;height:590px;writing-mode:vertical-rl;white-space:nowrap;font-family:"Raleway",Arial,sans-serif;font-weight:300;font-size:12px;letter-spacing:2.5px;color:var(--faint);text-transform:uppercase;text-align:center}
</style>
</head>
<body>
<main class="letterhead">
  <header>
    <div class="brand"><span class="brand-mark"></span><span class="brand-name">Brightfield Ventures</span></div>
    <div class="brand-rule"></div>
    <address class="contact">
      <div class="contact-name">Brightfield Ventures Inc.</div>
      <div class="contact-line">448 Willowmere Ave, Ste 210 <span class="dot"></span></div>
      <div class="contact-line">Alder Bay, CA 95999</div>
      <div class="contact-line">530-555-0187 <span class="dot"></span></div>
      <div class="contact-line">info@brightfieldventures.example <span class="dot"></span></div>
      <div class="contact-line">brightfieldventures.example <span class="dot"></span></div>
    </address>
  </header>

  <section class="body-copy">
    <p>Lorem Ipsum is simply dummy text of the printing and typesetting industry. Lorem Ipsum has been the industry's standard dummy text ever since the 1500s, when an unknown printer took a galley of type and scrambled it to make a type specimen book. It has survived not only five centuries, but also the leap into electronic typesetting, remaining essentially unchanged. It was popularised in the 1960s with the release of Letraset sheets containing Lorem Ipsum passages, and more recently with desktop publishing software like Aldus PageMaker including versions of Lorem Ipsum.</p>
    <p>It is a long established fact that a reader will be distracted by the readable content of a page when looking at its layout. The point of using Lorem Ipsum is that it has a more-or-less normal distribution of letters, as opposed to using 'Content here, content here', making it look like readable English. Many desktop publishing packages and web page editors now use Lorem Ipsum as their default model text, and a search for 'lorem ipsum' will uncover many web sites still in their infancy. Various versions have evolved over the years, sometimes by accident, sometimes on purpose (injected humour and the like).</p>
    <p>Contrary to popular belief, Lorem Ipsum is not simply random text. It has roots in a piece of classical Latin literature from 45 BC, making it over 2000 years old. Richard McClintock, a Latin professor at Hampden-Sydney College in Virginia, looked up one of the more obscure Latin words, consectetur, from a Lorem Ipsum passage, and going through the cites of the word in classical literature, discovered the undoubtable source. Lorem Ipsum comes from sections 1.10.32 and 1.10.33 of "de Finibus Bonorum et Malorum" structures, to generate Lorem Ipsum which looks reasonable. The generated Lorem Ipsum is therefore always free from repetition, injected humour, or non-characteristic words etc.</p>
  </section>

  <div class="signature" role="img" aria-label="Handwritten signature of the sender"></div>

  <svg class="corner" width="200" height="270" viewBox="0 0 200 270" aria-hidden="true">
    <polygon points="0,0 92,0 14,66 0,84" fill="var(--red)"/>
    <polygon points="0,18 30,18 150,270 0,270" fill="var(--navy)"/>
  </svg>

  <div class="watermark">Brightfield Ventures</div>
  <div class="slogan">Bringing builders together for a stronger, purposeful trade</div>
</main>
</body>
</html>
```